Corporate Business Card

Very professional, Modern, Not to busy, include phone address email, website
(253) 617-4930, 18761 52nd Avenue S, Kent, WA 98047, martin@plumlinegroup.com, varkoworks.com

Target Market(s)

Manufacturing

Industry/Entity Type

Aero, machining, manufacturing, Off road racing

Contact Information for Business Card

Phone, address email, website

```html
<!DOCTYPE html>
<html lang="en">
<head>
<meta charset="utf-8">
<title>Varko Works – Business Card</title>
<link href="https://fonts.googleapis.com/css2?family=Montserrat:wght@400;500;700;800&display=swap" rel="stylesheet">
<style>
  :root {
    --navy: #1f3468;
    --red: #cc1a1c;
    --white: #ffffff;
    --ink: #1a1a1a;
    --backdrop: #d6d4d3;
    --map-tone: #2a4078;
  }
  * { margin: 0; padding: 0; box-sizing: border-box; }
  html, body { width: 1200px; height: 884px; overflow: hidden; }
  body {
    background: var(--backdrop);
    font-family: "Montserrat", Arial, sans-serif;
    position: relative;
  }
  .card {
    position: absolute;
    width: 620px;
    height: 354px;
    overflow: hidden;
  }
  /* Front side */
  .card--front {
    left: 60px; top: 60px;
    background: var(--white);
  }
  .front-brand {
    position: absolute;
    left: 48px; top: 44px;
    font-weight: 800;
    font-size: 58px;
    letter-spacing: 1px;
    color: var(--navy);
    line-height: 1;
  }
  .front-rule {
    position: absolute;
    left: 48px; top: 126px;
    width: 150px; height: 2px;
    background: var(--navy);
  }
  .identity {
    position: absolute;
    left: 40px; top: 148px;
    width: 200px;
    text-align: right;
  }
  .identity__name {
    font-weight: 700;
    font-size: 24px;
    color: var(--navy);
    letter-spacing: 0.5px;
    white-space: nowrap;
    line-height: 1.2;
  }
  .identity__title {
    font-size: 14px;
    color: var(--ink);
    margin-top: 4px;
    white-space: nowrap;
  }
  .divider {
    position: absolute;
    left: 258px; top: 140px;
    width: 1.5px; height: 78px;
    background: var(--navy);
  }
  .contacts {
    position: absolute;
    left: 276px; top: 140px;
    list-style: none;
  }
  .contacts li {
    display: flex;
    align-items: center;
    gap: 8px;
    font-size: 15px;
    color: var(--ink);
    line-height: 26px;
    white-space: nowrap;
  }
  .contacts svg { width: 15px; height: 15px; flex: none; }
  .address {
    position: absolute;
    left: 150px; top: 240px;
    font-size: 15px;
    color: var(--ink);
    letter-spacing: 0.3px;
    white-space: nowrap;
  }
  .front-bands {
    position: absolute;
    left: 0; bottom: 0;
    width: 620px; height: 80px;
  }
  /* Back side */
  .card--back {
    left: 520px; top: 470px;
    background: var(--navy);
  }
  .world-map {
    position: absolute;
    left: 60px; top: 40px;
    width: 520px; height: 270px;
    border-radius: 40%;
    background: radial-gradient(ellipse at center, var(--map-tone) 0%, var(--navy) 70%);
  }
  .back-brand {
    position: absolute;
    left: 0; right: 0; top: 128px;
    text-align: center;
    font-weight: 800;
    font-size: 64px;
    letter-spacing: 1px;
    color: var(--white);
    line-height: 1;
  }
  .back-rule {
    position: absolute;
    left: 110px; top: 222px;
    width: 200px; height: 2px;
    background: var(--white);
  }
</style>
</head>
<body>

<section class="card card--front" aria-label="Business card front">
  <div class="front-brand">Varko Works</div>
  <div class="front-rule"></div>

  <div class="identity">
    <div class="identity__name">MARTIN HALE</div>
    <div class="identity__title">Managing Director</div>
  </div>

  <div class="divider"></div>

  <ul class="contacts">
    <li>
      <svg viewBox="0 0 16 16" aria-hidden="true"><path fill="#1f3468" d="M3.5 1.5l2.3 2.6-1.2 1.8c.9 2 2.5 3.6 4.5 4.5l1.8-1.2 2.6 2.3-1.4 2.2C7 13.4 2.6 9 1.3 3z"/></svg>
      (253) 617-4930
    </li>
    <li>
      <svg viewBox="0 0 16 16" aria-hidden="true"><rect x="1" y="3" width="14" height="10" fill="#1f3468"/><path d="M1 3l7 6 7-6" fill="none" stroke="#fff" stroke-width="1.2"/></svg>
      martin@plumlinegroup.com
    </li>
    <li>
      <svg viewBox="0 0 16 16" aria-hidden="true"><circle cx="8" cy="8" r="7" fill="#1f3468"/><path d="M1 8h14M8 1c-3 3-3 11 0 14M8 1c3 3 3 11 0 14" fill="none" stroke="#fff" stroke-width="0.9"/></svg>
      www.varkoworks.com
    </li>
  </ul>

  <div class="address">18761 52nd Avenue S, Kent, WA 98047</div>

  <svg class="front-bands" viewBox="0 0 620 80" aria-hidden="true">
    <polygon points="0,52 600,52 594,66 0,66" fill="#1f3468"/>
    <polygon points="402,52 436,8 480,8 446,52" fill="#1f3468"/>
    <polygon points="440,52 474,8 560,8 526,52" fill="#cc1a1c"/>
    <polygon points="548,52 582,8 620,8 620,52" fill="#1f3468"/>
  </svg>
</section>

<section class="card card--back" aria-label="Business card back">
  <div class="world-map" role="img" aria-label="Faint dotted world map in the background"></div>
  <div class="back-brand">Varko Works</div>
  <div class="back-rule"></div>
</section>

</body>
</html>
```